Create the ONLY Supplement line for Male Entrepreneurs! (Verity Nine MD)

I need a label designed for a new supplement brand that I am launching.

There are five products so need a design that I can simply change the wording for each individual product

The brand name is called verity nine MD. The focus is male entrepreneurial health.

Target audience is men 35 to 55.

Concepts: the healthier you are in body the more money you will make in business.

Concept to copy: I want to make a clean minimalistic label mimicking Lansworth MD (google it and you'll see what I mean)

Target Market(s)

male entrepreneurs 35-55

Industry/Entity Type

Health Supplement

Colors

Designer to choose colors to be used in the design.

Requirements
Must have
• Modern classy design, similar to Lansworth MD.
Nice to have
• Highlight that the supplement is Doctor Approved.
Should not have
• No loud colors. Present it as high class.

```html
<!DOCTYPE html>
<html lang="en">
<head>
<meta charset="utf-8">
<title>Verity Nine MD — Vitamins for Men Label</title>
<link rel="stylesheet" href="https://fonts.googleapis.com/css2?family=Montserrat:wght@300;400;500;600;700&display=swap">
<style>
  :root {
    --page-bg: #ffffff;
    --label-light: #dcdcdc;
    --label-mid: #cdcdcd;
    --label-dark: #c2c2c2;
    --ink-strong: #3a3a3a;
    --ink-heading: #5a5a5a;
    --ink-soft: #4f4f4f;
  }
  * { margin: 0; padding: 0; box-sizing: border-box; }
  html, body {
    width: 1200px;
    height: 1200px;
    overflow: hidden;
    background: var(--page-bg);
    font-family: "Montserrat", sans-serif;
  }
  .label {
    position: absolute;
    left: 190px;
    top: 75px;
    width: 820px;
    height: 1050px;
    background: linear-gradient(90deg, var(--label-mid) 0%, var(--label-light) 30%, var(--label-mid) 70%, var(--label-dark) 100%);
  }
  .brand-name {
    position: absolute;
    left: 360px;
    top: 120px;
    width: 370px;
    text-align: right;
    font-size: 50px;
    font-weight: 400;
    letter-spacing: -1px;
    color: var(--ink-strong);
    white-space: nowrap;
  }
  .male-icon {
    position: absolute;
    left: 168px;
    top: 362px;
    width: 92px;
    height: 100px;
  }
  .product-title {
    position: absolute;
    left: 138px;
    top: 508px;
    font-size: 78px;
    font-weight: 600;
    line-height: 108px;
    letter-spacing: 5px;
    color: var(--ink-heading);
    text-transform: uppercase;
  }
  .product-focus {
    position: absolute;
    left: 140px;
    top: 768px;
    font-size: 29px;
    font-weight: 300;
    letter-spacing: 3.4px;
    color: var(--ink-soft);
    text-transform: uppercase;
  }
  .divider {
    position: absolute;
    left: 140px;
    top: 843px;
    width: 580px;
    height: 10px;
    background: #4a4a4a;
  }
  .approval {
    position: absolute;
    left: 140px;
    top: 880px;
    font-size: 37px;
    font-weight: 500;
    color: var(--ink-soft);
  }
  .count {
    position: absolute;
    left: 140px;
    top: 948px;
    font-size: 30px;
    font-weight: 400;
    color: var(--ink-soft);
  }
</style>
</head>
<body>
  <main class="label">
    <div class="brand-name">verity nine MD</div>

    <svg class="male-icon" viewBox="0 0 92 100" aria-hidden="true">
      <circle cx="32" cy="66" r="25" fill="none" stroke="#5a5a5a" stroke-width="11"/>
      <line x1="50" y1="48" x2="82" y2="16" stroke="#5a5a5a" stroke-width="11"/>
      <polygon points="56,6 90,6 90,40" fill="#5a5a5a"/>
    </svg>

    <h1 class="product-title">Vitamins for<br>Men</h1>
    <p class="product-focus">Male Entrepreneurial Health</p>
    <div class="divider"></div>
    <p class="approval">Doctor Approved Supplement</p>
    <p class="count">60 capsules</p>
  </main>
</body>
</html>
```